Project Overview:
We are looking to create a website for a monthly subscription IPTV service in WordPress. The website should provide a seamless user experience for customers to sign up for the service and manage their account information. We need the following pages: Home Page, Product Page, Sign-Up Page, and Account Information Page.

Home Page:
The Home Page design should be simple and clean, with a dark theme and minimalistic design elements. We would like to include graphics of popular movie shows displayed on multiple devices. The page should highlight the key benefits and features of our service and provide a clear call-to-action for visitors to sign up.

Product Page:
The Product Page should provide detailed information about our subscription tiers and pricing plans. It should highlight the key features of each plan and provide a clear comparison between them. The page should also include a call-to-action button for visitors to sign up.

Sign-Up Page:
The Sign-Up Page is the conversion page where members will sign up for the service. It should collect the following information: Name, Phone Number, Email, Password, and Payment Information. The design should be simple, intuitive, and easy to use. It should highlight the benefits of our service and provide a clear call-to-action for visitors to sign up.

Account Information Page:
The Account Information Page should allow members to view and manage their account details. It should include the following information: Profile Image, Contact Details, Password Management, Payment Information Management, and Membership Expiration Date. The design should be user-friendly, intuitive, and easy to navigate.

Goals: The primary goal of the website is to provide an easy-to-use portal for customers to sign up for the service and manage their account information. The website should be user-friendly and visually appealing to attract potential customers.

Scope: The scope of the project includes designing a home page, a sign-up page, an account information page, and a payment information page. The website should be designed to be responsive and accessible on desktop and mobile devices.

Design Preferences: The design should be clean, modern, and visually appealing. The use of a color palette that is consistent with the brand identity is recommended. The website should be easy to navigate and provide a clear call-to-action for users to sign up for the service.

FYI: The subscription service I am designing a website for is related to an IPTV service. IPTV stands for Internet Protocol Television, which is a digital television broadcasting protocol that uses the internet to deliver TV programs and videos to viewers. The website will allow customers to sign up for the IPTV service and access their account information such as user name and password, membership tier, name, and payment details. Please let me know if you have any further questions, and I would be happy to provide more details. Thank you!

Dear Designers,

Thank you for your participation in our project. After reviewing the designs received so far, we have decided to update the brief to better reflect our needs and preferences. We apologize for any confusion this may cause, but we believe that these changes will result in better design submissions and a more successful project overall.

The updated brief is as follows:

We are looking to create a website for WordPress.

Also, here is the updated Brief.

Project Title: WordPress Website Design for Monthly Subscription IPTV Service

Project Overview:
We are looking to create a website for a monthly subscription IPTV service. The website should provide a seamless user experience for customers to sign up for the service and manage their account information. We need the following pages: Home Page, Product Page, Sign-Up Page, and Account Information Page.

Home Page:

Product Page:

Sign-Up Page:

Account Information Page:

Design Preferences:
We prefer a dark theme with minimalistic design elements and hits of our logo colors. The website should be easy to use and navigate, with clear calls-to-action and simple, intuitive forms. The design should be optimized for mobile devices and load quickly.

We hope that these updates provide you with a clearer understanding of our requirements and preferences. Please let us know if you have any questions or concerns. We look forward to seeing your revised designs.

Thank you again for your participation.
We will guarantee this project as soon as we see something we like that meets the updated requirements.

The website's target audience is individuals who are interested in subscribing to the monthly service.

4 page

• One item for sale and a client profile section.

```html
<!DOCTYPE html>
<html lang="en">
<head>
<meta charset="utf-8">
<title>NOVAVIEW – Unlimited TV Streaming</title>
<link href="https://fonts.googleapis.com/css2?family=Poppins:wght@400;500;600;700;800;900&display=swap" rel="stylesheet">
<style>
:root{
  --red:#ff0b0b;
  --red-deep:#a30b0b;
  --white:#ffffff;
  --text-soft:#d9d9d9;
  --bg-main:#222222;
  --bg-alt:#1b1b1b;
  --bg-faq:#171717;
  --bg-foot:#141414;
  --line:#3d3d3d;
}
*{margin:0;padding:0;box-sizing:border-box}
html,body{width:1200px;height:4246px;overflow:hidden;background:var(--bg-main)}
body{font-family:'Poppins',sans-serif;color:var(--white);position:relative}
.abs{position:absolute}
section,footer{position:absolute;left:0;width:1200px}

/* hero */
.hero{top:0;height:734px;background:linear-gradient(90deg,#b10d0d 0%,#7a0a0a 35%,#3a2a2a 60%,#2a2f38 100%)}
.hero-visual{position:absolute;left:560px;top:0;width:640px;height:734px;background:linear-gradient(120deg,rgba(60,40,40,.3),rgba(90,100,120,.5) 60%,rgba(40,45,55,.7))}
.brand{left:74px;top:58px;display:flex;align-items:center;gap:12px}
.brand-mark{width:20px;height:20px;background:var(--red)}
.brand-name{font-weight:800;font-size:46px;letter-spacing:1px;color:var(--white);line-height:1}
.btn-signin{left:923px;top:66px;width:140px;height:46px;border-radius:23px;background:var(--red);color:var(--white);font-weight:600;font-size:18px;display:flex;align-items:center;justify-content:center}
.menu{left:1098px;top:76px;width:28px}
.menu span{display:block;height:4px;background:var(--white);margin-bottom:6px;border-radius:1px}
.hero-title{left:74px;top:244px;font-weight:800;font-size:58px;line-height:63px;letter-spacing:.5px}
.hero-sub{left:74px;top:443px;width:540px;font-size:19px;line-height:31px;color:var(--white)}
.email-field{height:58px;border:2px solid var(--white);border-radius:29px;display:flex;align-items:center;padding-left:24px;font-size:13px;color:var(--white)}
.email-field .go{position:absolute;right:6px;top:5px;width:44px;height:44px;border-radius:50%;background:var(--red);display:flex;align-items:center;justify-content:center}
.hero .email-field{left:74px;top:522px;width:511px}

/* feature */
.features{top:734px;height:1076px;background:var(--bg-main)}
.feature-title{font-weight:800;font-size:60px;line-height:74px}
.red{color:var(--red)}
.body-copy{font-size:18px;line-height:32px;color:var(--white);width:470px}
.photo{position:absolute}

/* trending */
.trending{top:1810px;height:606px;background:var(--bg-alt)}
.section-title{font-weight:700;font-size:44px}
.nav-arrow{width:30px;height:30px;border-radius:50%;display:flex;align-items:center;justify-content:center}
.card{position:absolute;top:145px;width:242px}
.card-img{width:242px;height:183px}
.card-title{margin-top:34px;font-weight:700;font-size:19px}
.card-time{margin-top:4px;font-size:15px;color:var(--red);display:flex;align-items:center;gap:14px}
.card-time i{width:13px;height:13px;border-radius:50%;background:var(--red);display:inline-block}
.card-desc{margin-top:6px;font-size:15.5px;line-height:26px;color:var(--text-soft)}
.btn-sub{margin-top:22px;margin-left:-4px;width:132px;height:38px;border:1.5px solid var(--red);border-radius:19px;font-weight:600;font-size:12.5px;display:flex;align-items:center;justify-content:center}

/* download */
.download{top:2416px;height:571px;background:var(--bg-main)}

/* faq */
.faq{top:2987px;height:606px;background:var(--bg-faq)}
.faq-item{position:absolute;left:74px;width:1052px;font-size:17px}
.faq-item .q{display:flex;justify-content:space-between;align-items:center}
.faq-item .dot{width:17px;height:17px;border-radius:50%;background:var(--red);display:flex;align-items:center;justify-content:center}
.faq-line{position:absolute;left:74px;width:1052px;height:1px;background:var(--line)}
.faq-answer{margin-top:18px;font-size:16px;line-height:35px;color:var(--text-soft)}

/* join */
.join{top:3593px;height:316px;background:var(--bg-main);text-align:center}
.join .email-field{left:343px;top:191px;width:511px;border-color:#8a8a8a;text-align:left}

/* footer */
.site-footer{top:3909px;height:337px;background:var(--bg-foot)}
.foot-brand{left:74px;top:68px;display:flex;align-items:center;gap:10px}
.foot-brand .brand-name{font-size:48px}
.foot-copy{left:74px;top:160px;font-size:14px;line-height:28px;color:var(--text-soft)}
.social{left:74px;top:234px;display:flex;gap:9px}
.social span{width:40px;height:40px;border-radius:50%;border:2px solid var(--white)}
.foot-col{top:64px;font-size:15px;line-height:37px;color:var(--text-soft)}
</style>
</head>
<body>

<section class="hero">
  <div class="hero-visual" role="img" aria-label="Wall of TV show and movie thumbnails with a hand holding a remote control"></div>
  <div class="abs brand"><span class="brand-mark"></span><span class="brand-name">NOVAVIEW</span></div>
  <div class="abs btn-signin">Sign In</div>
  <div class="abs menu"><span></span><span></span><span></span></div>
  <h1 class="abs hero-title">Watch Unlimited TV<br>Shows &nbsp;Programs<br>and more</h1>
  <p class="abs hero-sub">Ready to watch? Enter your email to create or restart your membership.</p>
  <div class="abs email-field">Email Address
    <span class="go"><svg width="20" height="20" viewBox="0 0 20 20"><path d="M3 10h13M11 5l5 5-5 5" stroke="#fff" stroke-width="2.4" fill="none" stroke-linecap="round" stroke-linejoin="round"/></svg></span>
  </div>
</section>

<section class="features">
  <h2 class="abs feature-title" style="left:72px;top:134px">Enjoy your <span class="red">TV</span><br><span class="red">Programs</span></h2>
  <p class="abs body-copy" style="left:74px;top:312px">Nemo enim ipsam voluptatem quia voluptas sit aspernatur aut odit aut fugit, sed quia consequuntur magni dolores eos qui ratione voluptatem sequi nesciunt dicta sunt explicabo.</p>
  <div class="photo" style="left:615px;top:77px;width:511px;height:420px;background:linear-gradient(135deg,#cfc6bb,#8e8a86 55%,#5a6a80)" role="img" aria-label="Couple on a sofa watching a wall-mounted smart TV"></div>

  <div class="photo" style="left:74px;top:568px;width:509px;height:420px;background:linear-gradient(135deg,#6b5443,#a9a6a2 50%,#4f5a63)" role="img" aria-label="Man lying down watching a show on a laptop"></div>
  <h2 class="abs feature-title" style="left:613px;top:605px;line-height:61px">Watch Your<br><span class="red">TV Programs</span><br>Anywhere</h2>
  <p class="abs body-copy" style="left:614px;top:823px">Nemo enim ipsam voluptatem quia voluptas sit aspernatur aut odit aut fugit, sed quia consequuntur magni dolores eos qui ratione voluptatem sequi nesciunt dicta sunt explicabo.</p>
</section>

<section class="trending">
  <h2 class="abs section-title" style="left:74px;top:52px">Trending Programs</h2>
  <div class="abs nav-arrow" style="left:1048px;top:70px;background:#8a8a8a"><svg width="16" height="16" viewBox="0 0 16 16"><path d="M13 8H3M7 4L3 8l4 4" stroke="#222" stroke-width="2.2" fill="none" stroke-linecap="round"/></svg></div>
  <div class="abs nav-arrow" style="left:1096px;top:70px;background:var(--red)"><svg width="16" height="16" viewBox="0 0 16 16"><path d="M3 8h10M9 4l4 4-4 4" stroke="#222" stroke-width="2.2" fill="none" stroke-linecap="round"/></svg></div>

  <div class="card" style="left:74px">
    <div class="card-img" style="background:linear-gradient(135deg,#9aa7c0,#3a4a6a 60%,#c24a6a)" role="img" aria-label="Tablet showing a show on a person's lap"></div>
    <div class="card-title">Sed ut perspiciatis</div>
    <div class="card-time"><i></i>2h, 23min</div>
    <div class="card-desc">Nemo enim ipsam voluptatem quia voluptas sit aspernatur aut odit aut fugit</div>
    <div class="btn-sub">Subscribe Now</div>
  </div>
  <div class="card" style="left:344px">
    <div class="card-img" style="background:linear-gradient(135deg,#2c3550,#6a5040 55%,#b9874f)" role="img" aria-label="Friends watching TV together in a living room"></div>
    <div class="card-title">Sed ut perspiciatis</div>
    <div class="card-time"><i></i>2h, 23min</div>
    <div class="card-desc">Nemo enim ipsam voluptatem quia voluptas sit aspernatur aut odit aut fugit</div>
    <div class="btn-sub">Subscribe Now</div>
  </div>
  <div class="card" style="left:614px">
    <div class="card-img" style="background:linear-gradient(135deg,#1d1d22,#5a3a30 55%,#c9c9cc)" role="img" aria-label="TV screen showing a streaming menu of series"></div>
    <div class="card-title">Sed ut perspiciatis</div>
    <div class="card-time"><i></i>2h, 23min</div>
    <div class="card-desc">Nemo enim ipsam voluptatem quia voluptas sit aspernatur aut odit aut fugit</div>
    <div class="btn-sub">Subscribe Now</div>
  </div>
  <div class="card" style="left:885px">
    <div class="card-img" style="background:linear-gradient(135deg,#2f8aa0,#4a4a48 55%,#7a6a5a)" role="img" aria-label="TV on a blue wall showing a fantasy film title screen"></div>
    <div class="card-title">Sed ut perspiciatis</div>
    <div class="card-time"><i></i>2h, 23min</div>
    <div class="card-desc">Nemo enim ipsam voluptatem quia voluptas sit aspernatur aut odit aut fugit</div>
    <div class="btn-sub">Subscribe Now</div>
  </div>
</section>

<section class="download">
  <h2 class="abs feature-title" style="left:72px;top:102px"><span class="red">Download</span> your<br>shows to <span class="red">watch</span><br><span class="red">offline.</span></h2>
  <p class="abs body-copy" style="left:74px;top:340px">Nemo enim ipsam voluptatem quia voluptas sit aspernatur aut odit aut fugit, sed quia consequuntur magni dolores eos qui ratione voluptatem sequi nesciunt dicta sunt explicabo.</p>
  <div class="photo" style="left:615px;top:74px;width:511px;height:419px;background:linear-gradient(135deg,#2a3a40,#5a4a3a 55%,#a07a5a)" role="img" aria-label="Woman with headphones watching a show on her phone"></div>
</section>

<section class="faq">
  <h2 class="abs section-title" style="left:0;width:1200px;text-align:center;top:62px">Frequently Asked Questions</h2>
  <div class="faq-item" style="top:163px">
    <div class="q" style="font-weight:600">Sed ut perspiciatis unde omnis iste natus error sit voluptatem?<span class="dot"><svg width="9" height="9" viewBox="0 0 10 10"><path d="M1 5h7M5 2l3 3-3 3" stroke="#171717" stroke-width="1.8" fill="none"/></svg></span></div>
    <div class="faq-answer">Neque porro quisquam est, qui dolorem ipsum quia dolor sit amet, consectetur, adipisci velit, sed quia non numquam eius modi tempora incidunt ut labore et dolore magnam aliquam quaerat voluptatem.</div>
  </div>
  <div class="faq-line" style="top:288px"></div>
  <div class="faq-item" style="top:308px"><div class="q">Accusantium doloremque laudantium, totam rem aperiam eaque ipsa quae ab illo inventore?<span class="dot"><svg width="9" height="9" viewBox="0 0 10 10"><path d="M1 5h7M5 2l3 3-3 3" stroke="#171717" stroke-width="1.8" fill="none"/></svg></span></div></div>
  <div class="faq-line" style="top:354px"></div>
  <div class="faq-item" style="top:375px"><div class="q">Veritatis et quasi architecto beatae vitae dicta sunt explicabo?<span class="dot"><svg width="9" height="9" viewBox="0 0 10 10"><path d="M1 5h7M5 2l3 3-3 3" stroke="#171717" stroke-width="1.8" fill="none"/></svg></span></div></div>
  <div class="faq-line" style="top:420px"></div>
  <div class="faq-item" style="top:441px"><div class="q">Nemo enim ipsam voluptatem quia voluptas sit aspernatur aut odit aut fugit?<span class="dot"><svg width="9" height="9" viewBox="0 0 10 10"><path d="M1 5h7M5 2l3 3-3 3" stroke="#171717" stroke-width="1.8" fill="none"/></svg></span></div></div>
  <div class="faq-line" style="top:487px"></div>
  <div class="faq-item" style="top:507px"><div class="q">Veritatis et quasi architecto beatae vitae dicta sunt explicabo?<span class="dot"><svg width="9" height="9" viewBox="0 0 10 10"><path d="M1 5h7M5 2l3 3-3 3" stroke="#171717" stroke-width="1.8" fill="none"/></svg></span></div></div>
</section>

<section class="join">
  <h2 class="abs section-title" style="left:0;width:1200px;top:60px">Join Today Our Membership</h2>
  <p class="abs" style="left:0;width:1200px;top:138px;font-size:18px">Ready to watch? Enter your email to create or restart your membership.</p>
  <div class="abs email-field">Email Address
    <span class="go"><svg width="20" height="20" viewBox="0 0 20 20"><path d="M3 10h13M11 5l5 5-5 5" stroke="#fff" stroke-width="2.4" fill="none" stroke-linecap="round" stroke-linejoin="round"/></svg></span>
  </div>
</section>

<footer class="site-footer">
  <div class="abs foot-brand"><span class="brand-mark"></span><span class="brand-name">NV</span></div>
  <div class="abs foot-copy">Copyright © 2023 CompanyName<br>All Right Reserved</div>
  <div class="abs social"><span></span><span></span><span></span><span></span></div>
  <div class="abs foot-col" style="left:392px">FAQ<br>Help Centre<br>Account<br>Media Centre<br>Investor Relations<br>Jobs</div>
  <div class="abs foot-col" style="left:643px">Ways to Watch<br>Terms of Use<br>Privacy<br>Cookie Preferences<br>Corporate Information<br>Contact Us</div>
  <div class="abs foot-col" style="left:906px">Speed Test<br>Legal Notices<br>Only on NOVAVIEW</div>
</footer>

</body>
</html>
```